Brightwave Reach - Business Card

We need a business card for a Social Media Marketing company that specializes in online marketing for small businesses in Canada using common Social Media platforms such as Pixlora, Chatterly, Blinkpost & Quibber.

I have uploaded a copy of our logo which I would like utilized in the business card. We would like the business card to be modern yet classy design.

Our website is www.brightwavereach.ca

Industry/Entity Type

Marketing

Contact Information for Business Card

Email: info@brightwavereach.ca
Website: www.brightwavereach.ca
Telephone: 604-555-0193

Colors

Designer to choose colors to be used in the design.

Requirements
Must have
• Social Media icons on reverse
• Please add some designs with color.

```html
<!DOCTYPE html>
<html lang="en">
<head>
<meta charset="utf-8">
<title>Brightwave Reach – Business Card</title>
<link rel="stylesheet" href="https://fonts.googleapis.com/css2?family=Open+Sans:wght@400;600;800&display=swap">
<style>
  :root {
    --stage: #000000;
    --card-light: #f3f3f3;
    --card-dark: #3f4346;
    --ink: #4a4d50;
    --ink-strong: #1f2123;
    --ink-body: #2e3032;
    --paper: #f1f1f1;
    --accent-teal: #1fb5a8;
    --accent-coral: #f26b5b;
    --accent-amber: #f5b700;
    --accent-sky: #3a9ad9;
  }
  * { margin: 0; padding: 0; box-sizing: border-box; }
  html, body { width: 1200px; height: 900px; overflow: hidden; background: var(--stage); }
  body { position: relative; font-family: "Open Sans", Arial, sans-serif; }

  .card { position: absolute; top: 200px; width: 309px; height: 502px; overflow: hidden; }
  .card-front { left: 265px; background: var(--card-light); border-radius: 56px 0 56px 0; }
  .card-back { left: 641px; background: var(--card-dark); border-radius: 0 56px 0 56px; }

  .brand-name {
    position: absolute; left: 0; right: 0; text-align: center;
    font-weight: 800; text-transform: uppercase; line-height: 1.02; letter-spacing: 0.5px;
  }
  .card-front .brand-name { top: 78px; font-size: 33px; color: var(--ink); }
  .card-back .brand-name { top: 196px; font-size: 33px; color: var(--paper); }

  .holder { position: absolute; left: 23px; top: 357px; }
  .holder-name { font-size: 17px; font-weight: 600; color: var(--ink-strong); line-height: 1.2; }
  .holder-role { font-size: 13px; color: var(--ink-body); line-height: 1.3; }

  .contact-list { position: absolute; left: 24px; top: 414px; list-style: none; }
  .contact-item {
    display: flex; align-items: center; gap: 7px;
    font-size: 13px; color: var(--ink-body); height: 21px;
  }
  .contact-icon { width: 10px; height: 10px; fill: var(--ink-strong); }

  .accent-rule {
    position: absolute; left: 104px; width: 100px; height: 3px; top: 292px;
    background: linear-gradient(90deg, var(--accent-teal), var(--accent-sky), var(--accent-amber), var(--accent-coral));
    border-radius: 2px;
  }

  .social-list {
    position: absolute; left: 0; right: 0; top: 400px;
    display: grid; grid-template-columns: repeat(2, auto); justify-content: center;
    column-gap: 34px; row-gap: 10px; list-style: none;
  }
  .social-item {
    display: flex; align-items: center; gap: 8px;
    font-size: 13px; font-weight: 600; color: var(--paper);
  }
  .social-dot { width: 12px; height: 12px; border-radius: 50%; flex: none; }
  .dot-pixlora { background: var(--accent-coral); }
  .dot-chatterly { background: var(--accent-sky); }
  .dot-blinkpost { background: var(--accent-amber); }
  .dot-quibber { background: var(--accent-teal); }
</style>
</head>
<body>
  <section class="card card-front">
    <div class="brand-name">Brightwave<br>Reach</div>

    <div class="holder">
      <div class="holder-name">Daniel Marsh</div>
      <div class="holder-role">Managing Director</div>
    </div>

    <ul class="contact-list">
      <li class="contact-item">
        <svg class="contact-icon" viewBox="0 0 10 10" aria-hidden="true"><path d="M2 0.5 L3.6 2.6 L2.8 3.6 Q4 6 6.4 7.2 L7.4 6.4 L9.5 8 L8.6 9.5 Q3.5 9 0.5 1.4 Z"/></svg>
        <span>(604)-555-0193</span>
      </li>
      <li class="contact-item">
        <svg class="contact-icon" viewBox="0 0 10 10" aria-hidden="true"><path d="M0.5 2 H9.5 V8 H0.5 Z M1 2.4 L5 5.4 L9 2.4 V3.2 L5 6.2 L1 3.2 Z" fill-rule="evenodd"/></svg>
        <span>info@brightwavereach.ca</span>
      </li>
      <li class="contact-item">
        <svg class="contact-icon" viewBox="0 0 10 10" aria-hidden="true"><circle cx="5" cy="5" r="4.6"/><path d="M5 0.8 Q2.6 5 5 9.2 M5 0.8 Q7.4 5 5 9.2 M0.6 5 H9.4" stroke="#f3f3f3" stroke-width="0.8" fill="none"/></svg>
        <span>www.brightwavereach.ca</span>
      </li>
    </ul>
  </section>

  <section class="card card-back">
    <div class="brand-name">Brightwave<br>Reach</div>
    <div class="accent-rule"></div>

    <ul class="social-list" aria-label="Social channels">
      <li class="social-item"><span class="social-dot dot-pixlora"></span>Pixlora</li>
      <li class="social-item"><span class="social-dot dot-chatterly"></span>Chatterly</li>
      <li class="social-item"><span class="social-dot dot-blinkpost"></span>Blinkpost</li>
      <li class="social-item"><span class="social-dot dot-quibber"></span>Quibber</li>
    </ul>
  </section>
</body>
</html>
```